Redesign of the UI of a customer service platform

To improve the user experience of our customers, we need a new design for our agent interface of our customer service platform (velorant.com).
The focus will be on the dashboard and the inbox screens (see attached) along with the common UI elements (Buttons, menu, fonts, forms...)
We want a simple and distinctive design

Target Market(s)

Worldwide

Industry/Entity Type

It Service

Number of Pages Required

3 page

Font styles to use
Sans Serif

Requirements
Must have
• New Onboarding page: this is a new page that is shown to user the first time they login to the platform. This will replace the current onboarding screen (setup SMS, Setup widget...etc)
• Dashboard page: to access important information and activate services (see screenshot from current site)
• Inbox page: to manage all the interactions with customers. (see screenshot from current site)
• UI elements (buttons, menus, forms, tables, fonts, color palette)

```html
<!DOCTYPE html>
<html lang="en">
<head>
<meta charset="utf-8">
<title>velorant — Inbox</title>
<link href="https://fonts.googleapis.com/css2?family=Roboto:wght@400;500;700&display=swap" rel="stylesheet">
<style>
:root{
  --ink:#2b2b2b;
  --muted:#5a5a5a;
  --sidebar:#232323;
  --sidebar-icon:#2c2c2c;
  --accent:#e8363a;
  --accent-light:#ef5350;
  --page:#eceef2;
  --line:#d4d6da;
  --selected:#d9f1fb;
  --green:#2db54b;
  --blue:#3d94f6;
  --blue-pale:#9ccaf7;
  --red:#e8363a;
  --white:#fff;
}
*{box-sizing:border-box;margin:0;padding:0}
html,body{width:1200px;height:903px;overflow:hidden}
body{font-family:"Roboto",sans-serif;color:var(--ink);background:var(--page);position:relative}
svg{display:block}
.topbar{position:absolute;left:0;top:0;width:1200px;height:89px;background:var(--white)}
.brand{position:absolute;left:24px;top:24px;display:flex;align-items:center;gap:8px;font-size:31px;font-weight:700;color:var(--ink);letter-spacing:-.5px}
.brand-dot{width:24px;height:24px;border-radius:50%;background:var(--ink)}
.top-actions{position:absolute;right:40px;top:22px;display:flex;align-items:center;gap:22px;font-size:15px;color:var(--muted)}
.badge-wrap{position:relative}
.badge{position:absolute;top:-8px;left:0;background:var(--accent);color:#fff;font-size:11px;border-radius:9px;padding:1px 6px}
.status{display:flex;align-items:center;gap:6px}
.status i{width:10px;height:10px;border-radius:50%;background:#5fc35f;display:block}
.user-photo{width:44px;height:44px;background:linear-gradient(135deg,#c9b7a6,#6e5445)}
.caret{font-size:9px}
.sidebar{position:absolute;left:0;top:89px;width:209px;height:736px;background:var(--sidebar)}
.nav-item{display:flex;height:56px;border-bottom:1px solid #1b1b1b;color:#fff;font-size:19px;align-items:center}
.nav-icon{width:69px;height:100%;background:var(--sidebar-icon);display:flex;align-items:center;justify-content:center}
.nav-label{flex:1;padding-left:14px;display:flex;justify-content:space-between;padding-right:20px}
.nav-item.active{background:var(--accent-light)}
.nav-item.active .nav-icon{background:var(--accent)}
.feedback{position:absolute;left:0;top:771px;width:209px;height:54px;background:#2c2c2c;color:#fff;font-size:19px;display:flex;align-items:center;gap:14px;padding-left:22px}
.footer{position:absolute;left:0;top:825px;width:1200px;height:78px;background:var(--sidebar);color:#fff;font-size:13px;display:flex;align-items:center;justify-content:center}
.page-title{position:absolute;left:247px;top:110px;font-size:27px;font-weight:400;display:flex;gap:8px;align-items:center}
.tabs{position:absolute;left:249px;top:169px;display:flex;font-size:14px}
.tab{height:34px;padding:0 28px;display:flex;align-items:center}
.tab.active{background:#fff;border-top:2px solid var(--accent);border-left:1px solid var(--line);border-right:1px solid var(--line);padding:0 37px}
.panel{position:absolute;left:249px;top:203px;width:917px;height:543px;background:#fff;border:1px solid var(--line)}
.threads{position:absolute;left:0;top:0;width:325px;height:541px;background:#ececec}
.thread{height:59px;border-bottom:1px solid var(--line);background:#fff;display:flex;align-items:center;padding:0 18px 0 15px;font-size:13px;margin-top:12px}
.thread+.thread{margin-top:0}
.thread.selected{background:var(--selected)}
.avatar{width:34px;height:34px;border-radius:50%;background:radial-gradient(circle at 50% 40%,#c9a080,#5a3e2e);flex:none}
.thread-id{margin-left:17px;line-height:17px;color:var(--muted)}
.thread-name{margin-left:28px;flex:1;margin-top:-16px;color:var(--ink)}
.thread-meta{text-align:right;font-size:11px;color:var(--muted);line-height:18px}
.conv{position:absolute;left:344px;top:0;width:560px}
.conv-head{position:absolute;top:14px;left:0;width:560px;display:flex;align-items:center}
.conv-title{font-size:16px;display:flex;align-items:center;gap:7px}
.conv-title i{width:10px;height:10px;border-radius:50%;background:var(--red);display:block}
.btns{margin-left:auto;display:flex;gap:4px}
.btn{height:26px;padding:0 12px;color:#fff;font-size:12px;display:flex;align-items:center;border-radius:2px}
.btn.close{background:var(--green)}
.btn.transfer{background:var(--blue-pale)}
.btn.ban{background:var(--red)}
.chat{position:absolute;left:0;top:56px;width:561px;height:256px;border:1px solid var(--line);box-shadow:0 1px 2px rgba(0,0,0,.1);overflow:hidden}
.chat-bar{position:relative;z-index:2;height:26px;background:#f3f3f3;border-bottom:1px solid var(--line);display:flex;justify-content:space-between;align-items:center;padding:0 15px 0 17px;font-size:12.5px;color:#444}
.avatar.lg{position:absolute;width:49px;height:49px}
.bubble{position:absolute;border:1px solid var(--line);border-radius:3px;box-shadow:0 1px 2px rgba(0,0,0,.12);font-size:10.3px;line-height:15.5px;padding:7px 17px;color:#333;background:#fff}
.composer-bg{position:absolute;left:0;bottom:0;width:559px;height:35px;background:#f3f3f3}
.composer{position:absolute;left:10px;bottom:4px;width:540px;height:26px;border:1px solid var(--line);background:#fff;font-size:10.5px;color:#555;display:flex;align-items:center;justify-content:space-between;padding:0 10px}
.dtabs{position:absolute;left:1px;top:336px;display:flex;font-size:13px;color:#555}
.dtab{height:34px;padding:0 8px;display:flex;align-items:center;gap:4px}
.dtab.active{border-top:2px solid var(--accent);border-left:1px solid var(--line);border-right:1px solid var(--line);padding:0 15px;background:#fff;position:relative;top:1px}
.details{position:absolute;left:1px;top:365px;width:561px;height:162px;border:1px solid var(--line);box-shadow:0 1px 2px rgba(0,0,0,.1);font-size:13px;color:#333}
.fields{position:absolute;top:24px;line-height:23px}
.fields li{list-style:none;display:flex;gap:8px;align-items:center}
.fields svg{width:12px;height:12px;fill:#999}
.edit{position:absolute;right:10px;top:9px;background:var(--blue);color:#fff;font-size:12px;height:26px;padding:0 12px;border-radius:2px;display:flex;align-items:center;gap:5px}
</style>
</head>
<body>

<header class="topbar">
  <div class="brand"><span class="brand-dot"></span>velorant</div>
  <div class="top-actions">
    <div class="badge-wrap">
      <svg width="24" height="24" viewBox="0 0 24 24"><path d="M3 12l3-7h12l3 7v8H3z" fill="#555"/><path d="M3 12h5l1 3h6l1-3h5" fill="none" stroke="#fff" stroke-width="1.6"/></svg>
      <span class="badge">8</span>
    </div>
    <svg width="26" height="26" viewBox="0 0 24 24"><rect x="6" y="4" width="10" height="16" rx="1" transform="rotate(45 12 12)" fill="#555"/><line x1="9" y1="15" x2="15" y2="9" stroke="#fff" stroke-width="1.5" stroke-dasharray="2 1.5"/></svg>
    <div class="status"><i></i>Available <span class="caret">▼</span></div>
    <div class="user-photo" role="img" aria-label="Agent profile photo"></div>
    <div>Welcome, Elin <span class="caret">▼</span></div>
    <svg width="20" height="20" viewBox="0 0 20 20"><circle cx="10" cy="10" r="9" fill="#555"/><text x="10" y="15" text-anchor="middle" font-size="13" font-weight="700" fill="#fff" font-family="Roboto,sans-serif">?</text></svg>
  </div>
</header>

<nav class="sidebar">
  <div class="nav-item"><div class="nav-icon"><svg width="20" height="18" viewBox="0 0 20 18"><path d="M10 1L1 9h3v8h5v-5h2v5h5V9h3z" fill="#fff"/></svg></div><div class="nav-label">Dashboard<span>›</span></div></div>
  <div class="nav-item active"><div class="nav-icon"><svg width="20" height="18" viewBox="0 0 24 20"><path d="M2 10l3-8h14l3 8v8H2z" fill="#fff"/><path d="M2 11h6l1 3h6l1-3h6" fill="none" stroke="#e8363a" stroke-width="1.8"/></svg></div><div class="nav-label">Inbox<span>›</span></div></div>
  <div class="nav-item"><div class="nav-icon"><svg width="22" height="22" viewBox="0 0 24 24"><rect x="6" y="3" width="11" height="18" rx="1" transform="rotate(45 12 12)" fill="#fff"/></svg></div><div class="nav-label">Tickets<span>›</span></div></div>
  <div class="nav-item"><div class="nav-icon"><svg width="24" height="20" viewBox="0 0 24 20"><circle cx="12" cy="6" r="4" fill="#fff"/><circle cx="5" cy="8" r="3" fill="#fff"/><circle cx="19" cy="8" r="3" fill="#fff"/><path d="M5 19c0-5 3-8 7-8s7 3 7 8z" fill="#fff"/><path d="M0 18c0-4 2-6 5-6v6zM24 18c0-4-2-6-5-6v6z" fill="#fff"/></svg></div><div class="nav-label">Clients<span>›</span></div></div>
  <div class="nav-item"><div class="nav-icon"><svg width="24" height="20" viewBox="0 0 24 20"><path d="M1 1v18h22" fill="none" stroke="#fff" stroke-width="2"/><rect x="5" y="10" width="3" height="7" fill="#fff"/><rect x="10" y="5" width="3" height="12" fill="#fff"/><rect x="15" y="8" width="3" height="9" fill="#fff"/><rect x="19" y="3" width="3" height="14" fill="#fff"/></svg></div><div class="nav-label">Reports<span>›</span></div></div>
  <div class="nav-item"><div class="nav-icon"><svg width="24" height="22" viewBox="0 0 24 22"><circle cx="9" cy="12" r="6" fill="none" stroke="#fff" stroke-width="4" stroke-dasharray="3 2"/><circle cx="18" cy="6" r="3.5" fill="none" stroke="#fff" stroke-width="2.5" stroke-dasharray="2 1.5"/><circle cx="18" cy="17" r="3" fill="none" stroke="#fff" stroke-width="2.5" stroke-dasharray="2 1.5"/></svg></div><div class="nav-label">Settings<span>›</span></div></div>
</nav>
<div class="feedback"><svg width="22" height="16" viewBox="0 0 22 16"><rect x="1" y="1" width="20" height="14" rx="1" fill="none" stroke="#fff" stroke-width="1.8"/><path d="M1 2l10 8 10-8" fill="none" stroke="#fff" stroke-width="1.8"/></svg>Send Feedback</div>

<main>
  <h1 class="page-title"><svg width="22" height="18" viewBox="0 0 24 20"><path d="M2 10l3-8h14l3 8v8H2z" fill="#333"/><path d="M2 11h6l1 3h6l1-3h6" fill="none" stroke="#eceef2" stroke-width="1.8"/></svg>Inbox</h1>

  <div class="tabs">
    <div class="tab active">AGENT</div>
    <div class="tab">DEPARTMENT</div>
    <div class="tab">ACCOUNT</div>
  </div>

  <section class="panel">
    <div class="threads">
      <div class="thread selected"><div class="avatar" role="img" aria-label="Customer avatar"></div><div class="thread-id">#4<br>hello</div><div class="thread-name">Maren Holloway</div><div class="thread-meta">💬<br>21 days ago</div></div>
      <div class="thread"><div class="avatar" role="img" aria-label="Customer avatar"></div><div class="thread-id">#3<br>hello</div><div class="thread-name">Theo Brandis</div><div class="thread-meta">💬<br>25 days ago</div></div>
      <div class="thread"><div class="avatar" role="img" aria-label="Customer avatar"></div><div class="thread-id">#2<br>hello</div><div class="thread-name">Holloway</div><div class="thread-meta">💬<br>27 days ago</div></div>
      <div class="thread"><div class="avatar" role="img" aria-label="Customer avatar"></div><div class="thread-id">#1<br>hello</div><div class="thread-name">Maren Holloway</div><div class="thread-meta">💬<br>29 days ago</div></div>
    </div>

    <div class="conv">
      <div class="conv-head">
        <div class="conv-title"><i></i>#4 - Maren Holloway</div>
        <div class="btns"><span class="btn close">CLOSE</span><span class="btn transfer">TRANSFER</span><span class="btn ban">BAN</span></div>
      </div>

      <div class="chat">
        <div class="chat-bar"><span>⊞ More details</span><span>⤓ Save Transcript</span></div>
        <div class="avatar lg" role="img" aria-label="Customer avatar" style="left:9px;top:37px"></div>
        <div class="bubble" style="left:76px;top:38px;width:313px">Lorem Ipsum has been the industry's standard dummy text ever since the 1500s, when an unknown printer</div>
        <div class="bubble" style="left:171px;top:106px;width:301px">Neque porro quisquam est qui dolorem ipsum quia dolor sit amet, consectetur text ever since the 1500s, when</div>
        <div class="avatar lg" role="img" aria-label="Agent avatar" style="left:485px;top:103px"></div>
        <div class="composer-bg"></div>
        <div class="composer"><span>Type a message here...</span><svg width="11" height="11" viewBox="0 0 12 12"><path d="M11 1L1 6l4 1 1 4z" fill="#333"/></svg></div>
      </div>

      <div class="dtabs">
        <div class="dtab active">ⓘ Details</div>
        <div class="dtab">Tickets</div>
        <div class="dtab">◷ History</div>
      </div>
      <div class="details">
        <ul class="fields" style="left:17px">
          <li><svg viewBox="0 0 12 12"><path d="M1 11L6 1l5 10h-2L6 4 3 11z"/></svg>Maren Holloway</li>
          <li><svg viewBox="0 0 12 12"><rect x="0" y="2" width="12" height="8"/></svg>E-mail</li>
          <li><svg viewBox="0 0 12 12"><path d="M2 1l3 2-1 2c1 2 2 3 3 3l2-1 2 3-2 1C5 11 1 7 1 3z"/></svg>Phone</li>
        </ul>
        <ul class="fields" style="left:303px;top:28px">
          <li><svg viewBox="0 0 12 12"><path d="M6 0a4 4 0 00-4 4c0 3 4 8 4 8s4-5 4-8a4 4 0 00-4-4z"/></svg>Address</li>
          <li><svg viewBox="0 0 12 12"><path d="M11 1L1 6l4 1 1 4z"/></svg>City/down</li>
          <li><svg viewBox="0 0 12 12"><circle cx="6" cy="6" r="5.5"/></svg>Country</li>
        </ul>
        <span class="edit">✎ EDIT</span>
      </div>
    </div>
  </section>
</main>

<footer class="footer">Copyright © 2017. All Rights Reserved</footer>
</body>
</html>
```